VIP Card Design Project

uZorvo is a premium sneaker store selling brand name sneakers like Volta, Rexa, Kembro and etc. ( www.uzorvoshop.com ) We need to design a VIP card to promote one of our discount program called "Uzorvo VIP Band 17", which offers 24% discount off all full-priced items. The idea is because we have a "Peakline Gym center" (peaklinegym.com) next door and we are trying to design a discount program for people going to the fitness center.
The design is for the front of the card. The back will be black and white with benefits information and member information.
The front design need to include our logo, "VIP", "Band 17" and our web address "Uzorvo.com" and Chatterly and quibbr logo.
It will be a plastic card in the size of 3.375x2.125 (bleed size 3.5x2.25)

```html
<!DOCTYPE html>
<html lang="en">
<head>
<meta charset="utf-8">
<title>uZorvo VIP Band 17 Card</title>
<link rel="stylesheet" href="https://fonts.googleapis.com/css2?family=Arvo:wght@700&family=PT+Sans:wght@400;700&display=swap">
<style>
  :root {
    --page: #ecebe8;
    --card: #ffffff;
    --green-dark: #137233;
    --green-mid: #2f8f3e;
    --green-light: #5aab3a;
    --red: #d6202a;
    --red-dark: #8e0f14;
    --grey-band: #c9c9c9;
    --text-grey: #4a4a4a;
    --teal-shoe: #4f9fa2;
    --dark-shoe: #3a3530;
  }
  * { margin: 0; padding: 0; box-sizing: border-box; }
  html, body { width: 1200px; height: 435px; overflow: hidden; }
  body { background: var(--page); position: relative; font-family: "PT Sans", Arial, sans-serif; }

  .card {
    position: absolute;
    width: 510px;
    height: 320px;
    background: var(--card);
    box-shadow: 4px 6px 10px rgba(0,0,0,0.35);
    overflow: hidden;
  }
  .card-front { left: 55px; top: 57px; }
  .card-back { left: 645px; top: 60px; width: 508px; height: 318px; padding: 30px 28px 0 28px; }

  .front-art { position: absolute; inset: 0; }

  .brand-name {
    position: absolute; left: 22px; top: 20px;
    font-family: "Arvo", Georgia, serif; font-weight: 700;
    font-size: 46px; color: var(--green-light); letter-spacing: 1px;
  }
  .product-photo { position: absolute; left: 22px; width: 135px; height: 88px; }
  .photo-teal { top: 105px; background: linear-gradient(160deg, #c7a97a, var(--teal-shoe) 45%, #8c7a5e); }
  .photo-dark { top: 213px; background: linear-gradient(160deg, #b89a72, var(--dark-shoe) 50%, #d8c240 85%); }

  .member-line { color: var(--red); font-size: 12px; }
  .benefits-title { color: var(--red); font-weight: 700; font-size: 19px; margin: 10px 0 8px; }
  .benefits-intro { color: var(--text-grey); font-size: 13px; margin-bottom: 18px; }
  .benefit-list { list-style: none; color: var(--text-grey); font-size: 12.5px; line-height: 18px; }
  .benefit-list li { display: flex; margin-bottom: 5px; }
  .benefit-list .marker { color: var(--red); width: 14px; flex: none; }
</style>
</head>
<body>

<section class="card card-front">
  <svg class="front-art" width="510" height="320" viewBox="0 0 510 320">
    <defs>
      <linearGradient id="green-field" x1="0" y1="0" x2="1" y2="1">
        <stop offset="0" stop-color="var(--green-dark)"/>
        <stop offset="0.6" stop-color="var(--green-mid)"/>
        <stop offset="1" stop-color="var(--green-light)"/>
      </linearGradient>
      <linearGradient id="grey-band" x1="0" y1="0" x2="1" y2="0">
        <stop offset="0" stop-color="#ffffff"/>
        <stop offset="1" stop-color="var(--grey-band)"/>
      </linearGradient>
      <radialGradient id="burst" cx="0.4" cy="0.35" r="0.7">
        <stop offset="0" stop-color="#d4242b"/>
        <stop offset="1" stop-color="var(--red-dark)"/>
      </radialGradient>
      <path id="tagline-path" d="M 178 312 C 330 250 420 150 418 18"/>
    </defs>
    <path d="M 305 0 L 510 0 L 510 320 L 130 320 C 320 255 400 130 305 0 Z" fill="url(#grey-band)"/>
    <path d="M 355 0 L 510 0 L 510 320 L 185 320 C 360 255 440 140 355 0 Z" fill="url(#green-field)"/>
    <polygon fill="url(#burst)" points="213,141 222,152 235,147 238,161 252,163 247,176 258,186 247,196 252,209 238,211 235,225 222,220 213,231 204,220 191,225 188,211 174,209 179,196 168,186 179,176 174,163 188,161 191,147 204,152"/>
    <text x="213" y="194" text-anchor="middle" font-family="Arvo, Georgia, serif" font-weight="700" font-size="25" fill="#ffffff">24%</text>
    <text font-family="Arvo, Georgia, serif" font-weight="700" font-size="20" fill="var(--red)">
      <textPath href="#tagline-path">discount off all full-priced items.</textPath>
    </text>
    <rect x="398" y="206" width="12" height="12" fill="#ffffff"/>
    <text x="414" y="217" font-family="Arvo, Georgia, serif" font-weight="700" font-size="11" fill="#ffffff">quibbr</text>
    <rect x="398" y="224" width="12" height="12" fill="#ffffff"/>
    <text x="414" y="235" font-family="Arvo, Georgia, serif" font-weight="700" font-size="11" fill="#ffffff">Chatterly</text>
    <text x="315" y="268" font-family="Arvo, Georgia, serif" font-weight="700" font-size="18" fill="#ffffff">Uzorvo VIP Band 17</text>
    <text x="276" y="307" font-family="Arvo, Georgia, serif" font-weight="700" font-size="20" letter-spacing="1.5" fill="#ffffff">www.Uzorvo.com</text>
  </svg>
  <div class="brand-name">uZorvo</div>
  <div class="product-photo photo-teal" role="img" aria-label="Photo of a teal high-top basketball sneaker"></div>
  <div class="product-photo photo-dark" role="img" aria-label="Photo of a black and yellow high-top basketball sneaker"></div>
</section>

<section class="card card-back">
  <p class="member-line">Member Name :.......................................................Member ID :.......................................................</p>
  <h2 class="benefits-title">Benefits :-</h2>
  <p class="benefits-intro">The UZORVO Member Program entitles Members to the following benefits:</p>
  <ol class="benefit-list">
    <li><span class="marker">a.</span><span>20% OFF your entire first purchase after you sign up (Limited Time Offer).<br>Certain items are excluded from this offer. Please see stores for details.</span></li>
    <li><span class="marker">b.</span><span>10% OFF every purchase while being a member.<br>Certain items are excluded from this offer. Please see stores for details.</span></li>
    <li><span class="marker">c.</span><span>Additional 10% OFF and FREE SHIPPING when an item is out of stock<br>in store but can be shipped to you from another location.</span></li>
    <li><span class="marker">d.</span><span>Eligible to purchase exclusive items offered to members only.<br>Purchasing of exclusive items is limited to 1 item per member per 30 days.<br>Please see stores for details.</span></li>
  </ol>
</section>

</body>
</html>
```